Redesign current business card for food company

i would like to redesign my business card. our company is food company, our product range from chips, juices, milk and etc (mostly dried food stuff).
I want o keep same logo but , the rest is open to new design.
you can check at our website about our company www.orvelpantry.com

Target Market(s)

most of food company

Industry/Entity Type

Business

Contact Information for Business Card

I want to keep more to blue color...

Colors
3176b5
abd036

Requirements
Must have
• our old logo
Nice to have
• we do not mind to have nice material on bus card in order to accomplish nice design. for example: using spot uv, embossed and etc.

```html
<!DOCTYPE html>
<html lang="en">
<head>
<meta charset="utf-8">
<title>Orvel Business Card</title>
<link rel="stylesheet" href="https://fonts.googleapis.com/css2?family=Fira+Sans:wght@400;500;600&display=swap">
<style>
  :root {
    --stage: #222222;
    --paper: #ffffff;
    --navy: #2e3192;
    --blue: #3176b5;
    --cyan: #0bb0cc;
    --green: #3db54a;
    --green-light: #abd036;
    --ink: #111111;
  }
  * { margin: 0; padding: 0; box-sizing: border-box; }
  html, body { width: 1189px; height: 1200px; overflow: hidden; background: var(--stage); }
  body { position: relative; font-family: "Fira Sans", sans-serif; color: var(--ink); }

  .card {
    position: absolute; left: 171px; width: 856px; height: 488px;
    background: var(--paper); overflow: hidden;
    box-shadow: 6px 8px 14px rgba(0,0,0,0.6);
  }
  .card--front { top: 67px; }
  .card--back { top: 626px; }

  .stripe { position: absolute; left: 0; right: 0; }
  .card--front .stripe--blue {
    bottom: 52px; height: 14px;
    background: linear-gradient(90deg, var(--cyan), var(--blue) 50%, var(--navy));
  }
  .card--front .stripe--green {
    bottom: 0; height: 44px;
    background: linear-gradient(90deg, var(--green), var(--green-light));
  }
  .card--back .stripe--blue {
    top: 0; height: 56px;
    background: linear-gradient(90deg, var(--cyan), var(--blue) 50%, var(--navy));
  }
  .card--back .stripe--green {
    top: 64px; height: 10px;
    background: linear-gradient(90deg, var(--green), var(--green-light));
  }

  .brand {
    position: absolute; display: flex; align-items: center; gap: 14px;
    font-family: "Fira Sans", sans-serif; font-weight: 600; color: var(--navy);
    letter-spacing: -2px; line-height: 1;
  }
  .brand__dot { border-radius: 50%; background: var(--green); }
  .card--front .brand { left: 0; right: 0; top: 150px; justify-content: center; font-size: 150px; }
  .card--front .brand__dot { width: 30px; height: 30px; }
  .card--back .brand { right: 70px; top: 110px; font-size: 100px; }
  .card--back .brand__dot { width: 20px; height: 20px; }

  .company { position: absolute; left: 43px; top: 136px; font-size: 29px; font-weight: 500; }
  .person { position: absolute; left: 44px; top: 190px; }
  .person__name { font-size: 28px; font-weight: 500; line-height: 1.1; }
  .person__role { font-size: 23px; color: var(--green); line-height: 1.1; }

  .contacts { position: absolute; left: 45px; top: 276px; list-style: none; }
  .contacts li { display: flex; align-items: center; gap: 6px; font-size: 23px; height: 29px; }
  .contacts svg { width: 25px; height: 25px; flex: none; }

  .website { position: absolute; right: 60px; top: 363px; font-size: 22px; font-weight: 500; }
  .website__name { color: var(--green); font-weight: 400; }

  .address-bar {
    position: absolute; left: 0; right: 0; top: 413px; height: 63px;
    background: linear-gradient(90deg, var(--cyan) 0%, var(--blue) 55%, var(--navy) 100%);
    color: var(--paper); font-size: 23px; display: flex; align-items: center; justify-content: center;
  }
  .address-bar::after {
    content: ""; position: absolute; left: 0; right: 0; top: 63px; height: 12px;
    background: linear-gradient(90deg, var(--green), var(--green-light));
  }
</style>
</head>
<body>

<section class="card card--front">
  <div class="stripe stripe--blue"></div>
  <div class="stripe stripe--green"></div>
  <div class="brand"><span class="brand__dot"></span>orvel</div>
</section>

<section class="card card--back">
  <div class="stripe stripe--blue"></div>
  <div class="stripe stripe--green"></div>

  <div class="brand"><span class="brand__dot"></span>orvel</div>

  <h1 class="company">Orvel Enterprises Corp.</h1>
  <div class="person">
    <p class="person__name">Daniel Hartono</p>
    <p class="person__role">President</p>
  </div>

  <ul class="contacts">
    <li>
      <svg viewBox="0 0 24 24" aria-label="Phone"><rect width="24" height="24" fill="#3db54a"/><path d="M5 9c0-3 14-3 14 0v2h-4V9H9v2H5z M7 12h10l1 6H6z" fill="#fff"/></svg>
      555-014-2210
    </li>
    <li>
      <svg viewBox="0 0 24 24" aria-label="Fax"><rect width="24" height="24" fill="#3db54a"/><path d="M8 4h8v5H8z M5 10h14v7H5z M8 15h8v5H8z" fill="#fff"/></svg>
      555-014-2211
    </li>
    <li>
      <svg viewBox="0 0 24 24" aria-label="Mobile"><rect width="24" height="24" fill="#3db54a"/><rect x="8" y="4" width="8" height="16" rx="1.5" fill="#fff"/><rect x="9.5" y="6" width="5" height="5" fill="#3db54a"/></svg>
      555 019 4832
    </li>
    <li>
      <svg viewBox="0 0 24 24" aria-label="Email"><rect width="24" height="24" fill="#3db54a"/><rect x="4" y="7" width="16" height="11" fill="#fff"/><path d="M4 7l8 6 8-6 M4 18l6-5 M20 18l-6-5" stroke="#3db54a" stroke-width="1.2" fill="none"/></svg>
      Daniel@orvelpantry.com
    </li>
  </ul>

  <p class="website">www.<span class="website__name">orvelpantry</span>.com</p>

  <p class="address-bar">820 W. Maple St Fairview, CA 91700</p>
</section>

</body>
</html>
```